Corvelle Meadow Organic Flower Farm, Farmer Florist

I am a flower grower and florist, so I do everything from the field to the vase. I want to include my website, phone, email and instagram

```html
<!DOCTYPE html>
<html lang="en">
<head>
<meta charset="utf-8">
<title>Corvelle Meadow – Business Card</title>
<link rel="stylesheet" href="https://fonts.googleapis.com/css2?family=Cinzel:wght@400;500&family=Arimo:wght@400&display=swap">
<style>
  :root {
    --backdrop: #262626;
    --card: #0c0c0c;
    --green-deep: #5b8a3c;
    --green-light: #9cc46a;
    --text-grey: #b9b9b9;
    --divider: #3a3a3a;
  }
  * { box-sizing: border-box; margin: 0; padding: 0; }
  html, body {
    width: 1200px; height: 900px; overflow: hidden;
    background: var(--backdrop);
  }
  .canvas {
    width: 1200px; height: 900px;
    display: flex; flex-direction: column;
    align-items: center; justify-content: center; gap: 36px;
  }
  .card {
    width: 680px; height: 388px;
    background: var(--card);
    box-shadow: 0 18px 40px rgba(0,0,0,.55);
    position: relative;
  }
  /* logo lockup stand-in */
  .brand {
    display: flex; align-items: center; gap: 10px;
    font-family: "Cinzel", serif; font-weight: 400;
    color: var(--green-deep); letter-spacing: .06em;
    text-transform: uppercase; white-space: nowrap;
  }
  .brand-dot {
    width: 12px; height: 12px; border-radius: 50%;
    background: var(--green-deep); flex: none;
  }
  /* contact side */
  .card--contact { display: flex; }
  .card__brand-panel {
    width: 50%; padding: 60px 32px 0;
    display: flex; align-items: center; justify-content: center;
  }
  .card__brand-panel .brand { font-size: 20px; }
  .card__divider {
    width: 1px; background: var(--divider);
    margin: 82px 0 70px;
  }
  .card__details {
    flex: 1; padding: 88px 0 0 38px;
  }
  .person__name {
    font-family: "Cinzel", serif; font-weight: 500;
    font-size: 24px; color: var(--green-deep);
    letter-spacing: .04em; text-transform: uppercase;
  }
  .person__role {
    font-family: "Arimo", sans-serif; font-size: 18px;
    color: var(--text-grey); margin-top: 2px;
  }
  .contact-list { list-style: none; margin-top: 30px; }
  .contact-list li {
    display: flex; align-items: center; gap: 10px;
    font-family: "Arimo", sans-serif; font-size: 18px;
    color: var(--text-grey); line-height: 1.5;
  }
  .contact-list svg { width: 18px; height: 18px; flex: none; }
  .contact-list .accent { color: var(--green-light); }
  .social-dot {
    width: 16px; height: 16px; border-radius: 50%;
    border: 2px solid var(--green-deep); flex: none; margin: 0 1px;
  }
  /* front side */
  .card--front { display: flex; align-items: center; justify-content: center; }
  .card--front .brand { font-size: 44px; gap: 16px; }
  .card--front .brand-dot { width: 18px; height: 18px; }
</style>
</head>
<body>
<main class="canvas">
  <section class="card card--contact" aria-label="Business card, contact side">
    <div class="card__brand-panel">
      <div class="brand"><span class="brand-dot"></span>Corvelle Meadow</div>
    </div>
    <div class="card__divider"></div>
    <div class="card__details">
      <h1 class="person__name">Harlan Reeve</h1>
      <p class="person__role">Managing Director</p>
      <ul class="contact-list">
        <li>
          <svg viewBox="0 0 24 24" fill="none" stroke="var(--green-deep)" stroke-width="2.4" stroke-linecap="round"><path d="M5 4h4l2 5-2.5 1.5a11 11 0 0 0 5 5L15 13l5 2v4a2 2 0 0 1-2 2A16 16 0 0 1 3 6a2 2 0 0 1 2-2z"/></svg>
          044-555 201 348
        </li>
        <li>
          <svg viewBox="0 0 24 24" fill="var(--green-deep)"><rect x="2" y="5" width="20" height="14" rx="1"/><path d="M2 6l10 7 10-7" fill="none" stroke="var(--card)" stroke-width="1.6"/></svg>
          hello@corvellemeadow.com
        </li>
        <li>
          <svg viewBox="0 0 24 24" fill="none" stroke="var(--green-deep)" stroke-width="2"><circle cx="12" cy="12" r="9"/><path d="M3 12h18M12 3c3 3 3 15 0 18M12 3c-3 3-3 15 0 18"/></svg>
          <span>www.<span class="accent">corvellemeadow</span>.com</span>
        </li>
        <li>
          <span class="social-dot"></span>
          @corvellemeadow
        </li>
      </ul>
    </div>
  </section>

  <section class="card card--front" aria-label="Business card, brand side">
    <div class="brand"><span class="brand-dot"></span>Corvelle Meadow</div>
  </section>
</main>
</body>
</html>
```